Lucky Harbour Fun Casino Entertainment

Looking to update my business card and make it look more modern, stand out and eye catching.
We are are fun casino business in Australia (primarily Sydney). Blackjack and Roulette are our most popular games although we have pretty much every game available for hire that you would find in a real casino. The final design would need to be sleek and appeal to the more upmarket corporate sector.
We mainly cater for Corporate Events, Private Parties, Fundraising Events, Team Building, Poker Tournaments
I think I'd prefer the colour Black.

Target Market(s)

High-end Corporate

Industry/Entity Type

Events

Contact Information for Business Card

Rob Kendall
Director
1300 482 617
0433 728 591
info@luckyharbour.com.au
www.luckyharbour.com.au
Facebook & Instagram @luckyharbourevents (proper social icons preferred)

Colors
000000
0255a3

Requirements
Must have
• Front side:
• Logo
• Contact details
• 'Australia's #1 Fun Casino Specialists'
• Back:
• Logo
Nice to have
• Back:
• Corporate Events
• Private Parties
• Poker Tournaments
• Fundraising
• Props & Theming
• Photo Booth
• Horse Racing Events
• The Vegas Sign attached, maybe on the back of the card in the background...?

```html
<!DOCTYPE html>
<html lang="en">
<head>
<meta charset="utf-8">
<title>Lucky Harbour – Business Card</title>
<link href="https://fonts.googleapis.com/css2?family=Open+Sans:wght@400&family=Roboto:wght@400;500;700&display=swap" rel="stylesheet">
<style>
  :root {
    --backdrop: #5e5e5e;
    --card: #0a0a0a;
    --gold: #f7b21b;
    --text: #e6e6e6;
    --muted: #b9b9b9;
    --rule: #4a4a4a;
  }
  * { margin: 0; padding: 0; box-sizing: border-box; }
  html, body { width: 1200px; height: 802px; overflow: hidden; }
  body { background: var(--backdrop); position: relative; font-family: "Open Sans", sans-serif; }

  .card {
    position: absolute; top: 274px; width: 442px; height: 265px;
    background: var(--card);
    box-shadow: 3px 4px 8px rgba(0,0,0,.45);
  }
  .card--front { left: 136px; }
  .card--back { left: 624px; }

  /* Front */
  .brand {
    position: absolute; left: 30px; top: 104px; width: 172px;
    display: flex; align-items: center; gap: 8px;
    font-family: "Roboto", sans-serif; font-weight: 700; font-size: 19px;
    color: var(--gold); letter-spacing: .5px; text-transform: uppercase; line-height: 1.1;
  }
  .brand__dot { width: 26px; height: 26px; border-radius: 50%; background: var(--gold); flex: none; }

  .divider-v { position: absolute; left: 220px; top: 79px; width: 1px; height: 111px; background: var(--rule); }

  .person { position: absolute; left: 240px; top: 75px; }
  .person__name { font-family: "Roboto", sans-serif; font-weight: 500; font-size: 20px; color: var(--gold); line-height: 1.1; }
  .person__role { font-size: 13px; color: var(--muted); line-height: 1.2; }

  .contacts { position: absolute; left: 240px; top: 126px; list-style: none; }
  .contacts li { display: flex; align-items: center; gap: 3px; height: 16.7px; font-size: 13px; color: var(--muted); }
  .contacts svg { width: 14px; height: 14px; flex: none; }

  .social {
    position: absolute; left: 37px; top: 209px; width: 364px; height: 16px;
  }
  .social::before {
    content: ""; position: absolute; left: 0; right: 0; top: 8px; height: 1px; background: var(--rule);
  }
  .social__icons {
    position: absolute; left: 50%; top: 0; transform: translateX(-50%);
    display: flex; gap: 4px; background: var(--card); padding: 0 3px;
  }
  .social__icons span { width: 16px; height: 16px; border-radius: 50%; background: var(--gold); }
  .social__handle { position: absolute; left: 0; right: 0; top: 226px; text-align: center; font-size: 13px; color: var(--text); }

  /* Back */
  .services {
    position: absolute; left: 0; right: 0; top: 70px; list-style: none; text-align: center;
    font-family: "Roboto", sans-serif; font-size: 13px; color: #f2f2f2; line-height: 18px;
  }
  .divider-h { position: absolute; left: 72px; width: 291px; top: 211px; height: 1px; background: var(--rule); }
  .tagline {
    position: absolute; left: 0; right: 0; top: 218px; text-align: center;
    font-family: "Roboto", sans-serif; font-size: 15px; color: var(--gold); letter-spacing: .2px;
  }
</style>
</head>
<body>

<section class="card card--front" aria-label="Business card front">
  <div class="brand"><span class="brand__dot"></span><span>Lucky Harbour</span></div>
  <div class="divider-v"></div>

  <div class="person">
    <p class="person__name">ROB KENDALL</p>
    <p class="person__role">Director</p>
  </div>

  <ul class="contacts">
    <li>
      <svg viewBox="0 0 14 14" aria-hidden="true"><circle cx="7" cy="7" r="7" fill="var(--gold)"/><path d="M3.5 6.5c0-1.5 1.5-2.5 3.5-2.5s3.5 1 3.5 2.5H9V5.6H5v.9z M4.5 7h5l.7 3H3.8z" fill="#0a0a0a"/></svg>
      <span>1300 482 617</span>
    </li>
    <li>
      <svg viewBox="0 0 14 14" aria-hidden="true"><circle cx="7" cy="7" r="7" fill="var(--gold)"/><rect x="4.6" y="3" width="4.8" height="8" rx=".8" fill="#0a0a0a"/><rect x="5.4" y="4" width="3.2" height="5" fill="var(--gold)"/></svg>
      <span>0433 728 591</span>
    </li>
    <li>
      <svg viewBox="0 0 14 14" aria-hidden="true"><circle cx="7" cy="7" r="7" fill="var(--gold)"/><rect x="3.5" y="4.5" width="7" height="5" fill="none" stroke="#0a0a0a" stroke-width="1"/><path d="M3.5 4.5L7 7.5l3.5-3" fill="none" stroke="#0a0a0a" stroke-width="1"/></svg>
      <span>info@luckyharbour.com.au</span>
    </li>
    <li>
      <svg viewBox="0 0 14 14" aria-hidden="true"><circle cx="7" cy="7" r="7" fill="var(--gold)"/><circle cx="7" cy="7" r="3.8" fill="none" stroke="#0a0a0a" stroke-width="1"/><path d="M3.2 7h7.6M7 3.2c-2 2.2-2 5.4 0 7.6M7 3.2c2 2.2 2 5.4 0 7.6" fill="none" stroke="#0a0a0a" stroke-width=".8"/></svg>
      <span>www.luckyharbour.com.au</span>
    </li>
  </ul>

  <div class="social">
    <div class="social__icons"><span></span><span></span></div>
  </div>
  <p class="social__handle">@luckyharbourevents</p>
</section>

<section class="card card--back" aria-label="Business card back">
  <ul class="services">
    <li>CORPORATE EVENTS</li>
    <li>PRIVATE PARTIES</li>
    <li>POKER TOURNAMENTS</li>
    <li>FUNDRAISING</li>
    <li>PROPS &amp; THEMING</li>
    <li>PHOTO BOOTH</li>
    <li>HORSE RACING EVENTS</li>
  </ul>
  <div class="divider-h"></div>
  <p class="tagline">AUSTRALIA’S #1 FUN CASINO SPECIALISTS</p>
</section>

</body>
</html>
```